KAJU Freightways #ALLKAJU Business Cards & Letterhead

I am looking to business cards designed for our organization. We are currently undergoing a small re-branding that is taking place. Our organization is called KAJU Freightways and we are headquartered in Phoenix, AZ. We primarily provide transportation and logistics services to the Marlow Parcel Bureau who is our largest customer. I would like to see a design that incorporates name, title, contact info, website, and address (this will be different depending on the employee). I would also like to see some color on the business card using our logo colors or a variation. I would like our logo on the back of the business card with the website displayed. The final design should communicate that we are a next generation transportation operate that focuses on being driver-first, customer-centric, innovative, and sustainable.We would also like our #ALLKAJU catch phrase incorporated as well.

Target Market(s)

Transportation & Logistics

Industry/Entity Type

Trucking Company

Contact Information for Business Card

-First and Last Name
-Position Title
-Contact Phone
-Contact Email
-Physical Address

Font styles to use
Serif

Colors

Designer to choose colors to be used in the design.

Requirements
Must have
• -KAJU logo prominently displayed
• -#ALLKAJU catch phrase used
• -Some amount of color, design gradient, etc.
• -Logo on the back with website listed (https://www.kajufreightco.example)

```html
<!DOCTYPE html>
<html lang="en">
<head>
<meta charset="UTF-8">
<title>KAJU Freightways Business Card</title>
<link rel="stylesheet" href="https://fonts.googleapis.com/css2?family=Roboto+Slab:wght@400;500;700;900&display=swap">
<style>
  :root {
    --teal: #033845;
    --teal-mid: #0b4350;
    --green: #6cbf2f;
    --paper: #ffffff;
    --ink: #3a3f44;
    --backdrop: #e6e8ea;
    --ring: #9aa4a8;
  }
  * { margin: 0; padding: 0; box-sizing: border-box; }
  html, body { width: 1200px; height: 960px; overflow: hidden; }
  body {
    background: var(--backdrop);
    font-family: "Roboto Slab", Georgia, serif;
    position: relative;
  }
  .card {
    position: absolute;
    width: 600px;
    height: 343px;
    box-shadow: 0 10px 28px rgba(0,0,0,0.18);
    overflow: hidden;
  }
  /* Back of card */
  .card-back {
    left: 540px; top: 70px;
    background: var(--teal-mid);
    display: flex; flex-direction: column; align-items: center; justify-content: center;
  }
  .back-mark {
    width: 180px; height: 180px;
    border: 5px solid var(--ring);
    border-radius: 50%;
    display: flex; align-items: center; justify-content: center;
  }
  .back-mark .wordmark {
    font-weight: 900; font-size: 46px; color: var(--ring); letter-spacing: 1px;
  }
  .back-tagline {
    margin-top: 18px;
    font-weight: 700; font-size: 16px; color: var(--green); letter-spacing: 3px;
  }
  .back-website {
    margin-top: 6px;
    font-size: 12px; color: #d7dee0; letter-spacing: 2px;
  }
  /* Front of card */
  .card-front {
    left: 60px; top: 500px;
    background: var(--paper);
  }
  .front-band { position: absolute; left: 0; bottom: 0; }
  .website {
    position: absolute; left: 22px; bottom: 18px;
    color: #ffffff; font-size: 12.5px; letter-spacing: 2.5px;
  }
  .contact {
    position: absolute; left: 30px; top: 148px;
    color: var(--ink); font-size: 13px; line-height: 19px;
  }
  .contact .address { margin-bottom: 6px; }
  .contact .line { display: flex; align-items: center; gap: 8px; }
  .contact svg { width: 11px; height: 11px; fill: var(--teal); flex: none; }
  .identity {
    position: absolute; right: 46px; top: 70px; text-align: right;
  }
  .identity .wordmark {
    font-weight: 900; font-size: 84px; line-height: 1; color: var(--teal); letter-spacing: 1px;
  }
  .identity .person {
    margin-top: 12px; font-weight: 700; font-size: 21px; color: var(--teal); letter-spacing: 0.5px;
  }
  .identity .role {
    font-weight: 500; font-size: 16px; color: var(--green);
  }
</style>
</head>
<body>
  <section class="card card-back" aria-label="Business card back">
    <div class="back-mark"><span class="wordmark">KAJU</span></div>
    <div class="back-tagline">#ALLKAJU</div>
    <div class="back-website">www.kajufreightco.example</div>
  </section>

  <section class="card card-front" aria-label="Business card front">
    <div class="identity">
      <div class="wordmark">KAJU</div>
      <div class="person">DANIEL REYES</div>
      <div class="role">President</div>
    </div>

    <div class="contact">
      <div class="address">4120 Cedar Hollow Road<br>Phoenix, Arizona 85004</div>
      <div class="line">
        <svg viewBox="0 0 24 24"><path d="M6.6 10.8a15.1 15.1 0 0 0 6.6 6.6l2.2-2.2a1 1 0 0 1 1-.25 11.4 11.4 0 0 0 3.6.57 1 1 0 0 1 1 1V20a1 1 0 0 1-1 1A17 17 0 0 1 3 4a1 1 0 0 1 1-1h3.5a1 1 0 0 1 1 1c0 1.25.2 2.45.57 3.57a1 1 0 0 1-.25 1z"/></svg>
        <span>555-214-0187</span>
      </div>
      <div class="line">
        <svg viewBox="0 0 24 24"><path d="M2 5h20v14H2z M2 5l10 8 10-8" /></svg>
        <span>d.reyes@kajufreightco.example</span>
      </div>
    </div>

    <svg class="front-band" width="600" height="343" viewBox="0 0 600 343">
      <polygon points="0,270 300,270 318,300 600,300 600,343 0,343" fill="var(--teal)"/>
      <polygon points="322,292 600,292 600,297 325,297" fill="var(--green)"/>
    </svg>
    <div class="website">www.kajufreightco.example</div>
  </section>
</body>
</html>
```